We are a local Communty Pharmacy wishing to promote and market a specialised Pharmaceutical Service

We would like a design that is professional and enticing ( according to the brief In attached files)
We wish to Market Compounding Pharmacy as a specialist side of our business.
We have the expertise a purpose built preparation laboratory.
The main purpose is an Internet presence that entices prospective patients to contact or visit our physical store.

Target Market(s)

Patients Medicos and Veterinary clients

Industry/Entity Type

Pharmacy

Coding

Coded - Design and coding required

Number of Pages Required

1 page

Requirements
Must have
• Clear friendly image
Nice to have
• soft enticing feel
Should not have
• No crass loud unprofessional elements

```html
<!DOCTYPE html>
<html lang="en">
<head>
<meta charset="utf-8">
<title>Kestrel Pharmacy – Compounding Pharmacy</title>
<link href="https://fonts.googleapis.com/css2?family=Open+Sans:wght@400;600;700;800&display=swap" rel="stylesheet">
<style>
:root{
  --blue:#1f7fc4;
  --blue-dark:#15639c;
  --blue-deep:#0f4f80;
  --orange:#f5a11c;
  --text:#555;
  --heading:#2b3a4a;
  --light:#f1f3f5;
  --white:#fff;
}
*{box-sizing:border-box;margin:0;padding:0}
html,body{width:766px;height:1200px;overflow:hidden}
body{font-family:"Open Sans",Arial,sans-serif;color:var(--text);background:var(--white);position:relative}

.site-header{height:76px;display:flex;justify-content:space-between;align-items:center;padding:0 40px}
.brand{display:flex;align-items:center;gap:8px}
.brand-mark{width:22px;height:22px;background:var(--blue)}
.brand-name{font-weight:800;font-size:19px;color:var(--blue);letter-spacing:.5px}
.header-contact{font-size:7.5px;line-height:1.5;color:#666;display:grid;grid-template-columns:auto auto;column-gap:24px}
.header-contact strong{grid-column:1/3;font-size:9px;color:var(--heading);margin-bottom:2px}
.header-contact span{display:flex;align-items:center;gap:4px}
.header-contact svg{width:8px;height:8px;fill:var(--blue)}

.main-nav{height:26px;background:linear-gradient(var(--blue),var(--blue-dark));display:flex;padding-left:40px}
.main-nav a{display:flex;align-items:center;padding:0 22px;font-size:8px;font-weight:700;color:var(--white);text-decoration:none;border-right:1px solid rgba(255,255,255,.18)}
.main-nav a.active{background:var(--orange)}

.hero{position:relative;height:288px;overflow:hidden;
  background:
    radial-gradient(ellipse 260px 220px at 170px 120px,rgba(90,110,130,.55),rgba(90,110,130,0) 70%),
    radial-gradient(ellipse 200px 160px at 60px 250px,rgba(60,80,100,.45),rgba(60,80,100,0) 70%),
    radial-gradient(ellipse 240px 200px at 700px 60px,rgba(70,140,200,.35),rgba(70,140,200,0) 70%),
    linear-gradient(100deg,#b9c7d2 0%,#dbe4ea 35%,#f4f7f9 58%,#dde8f0 100%)}
.hero-text{position:absolute;left:357px;top:118px}
.hero-text h1{font-size:23px;font-weight:800;color:var(--blue-deep);letter-spacing:.3px}
.hero-text h2{font-size:13px;font-weight:700;color:var(--orange);margin-top:2px}
.btn{display:inline-block;background:var(--orange);color:var(--white);font-size:7px;font-weight:700;padding:7px 14px;margin-top:14px}
.hero-arrow{position:absolute;top:136px;width:16px;height:16px;border-radius:50%;background:rgba(60,70,80,.55);display:flex;align-items:center;justify-content:center}
.hero-arrow svg{width:6px;height:8px;fill:var(--white)}
.hero-arrow.prev{left:8px}.hero-arrow.next{right:8px}

.intro{text-align:center;padding:24px 110px 0;height:100px}
.intro h3{font-size:14px;font-weight:800;color:var(--heading)}
.intro h3::after{content:"";display:block;width:40px;height:2px;background:var(--orange);margin:7px auto 9px}
.intro p{font-size:7px;line-height:1.6}

.values{display:flex;justify-content:space-between;padding:16px 40px 0;height:175px}
.value{width:120px;text-align:center}
.value-icon{width:64px;height:64px;border-radius:50%;background:var(--blue);margin:0 auto 14px;display:flex;align-items:center;justify-content:center;box-shadow:0 0 0 4px #d7e8f5}
.value-icon svg{width:28px;height:28px;fill:none;stroke:var(--white);stroke-width:2;stroke-linecap:round;stroke-linejoin:round}
.value h4{font-size:7.5px;font-weight:800;color:var(--heading);line-height:1.35}

.features{background:var(--light);height:310px;padding:18px 40px 0;position:relative}
.features h3{text-align:center;font-size:15px;font-weight:700;color:var(--heading)}
.features h3::after{content:"";display:block;width:40px;height:2px;background:var(--orange);margin:6px auto 0}
.cards{display:flex;gap:18px;margin-top:14px}
.card{flex:1}
.card-photo{height:120px}
.card-photo.vet{background:linear-gradient(135deg,#e7d9c7,#b9c8d4)}
.card-photo.oral{background:linear-gradient(135deg,#d8c0b0,#9fb7c8)}
.card-photo.thyroid{background:linear-gradient(135deg,#e0d2c8,#a8bfd0)}
.card h5{font-size:9px;font-weight:700;color:var(--blue);margin-top:9px}
.card p{font-size:6.5px;line-height:1.55;margin-top:4px}
.card .more{display:inline-block;font-size:6.5px;font-weight:700;color:var(--orange);margin-top:5px}
.slider-dots{position:absolute;left:0;right:0;bottom:14px;display:flex;justify-content:center;gap:6px}
.slider-dots span{width:14px;height:14px;border-radius:50%;background:#9aa3ab;display:flex;align-items:center;justify-content:center}
.slider-dots svg{width:5px;height:7px;fill:var(--white)}

.site-footer{background:var(--blue);height:189px;display:flex;gap:22px;padding:18px 40px 0;color:var(--white)}
.footer-col{flex:1}
.footer-col h6{font-size:10px;font-weight:700;display:flex;align-items:center;gap:6px;margin-bottom:12px}
.footer-col h6 svg{width:10px;height:10px;fill:var(--white)}
.hours{width:100%;font-size:6.5px;border-collapse:collapse}
.hours td{padding:6px 0;border-bottom:1px solid rgba(255,255,255,.2)}
.hours td:last-child{text-align:right}
.map{height:120px;background:linear-gradient(135deg,#e9ecee,#cdd4d9);border:3px solid var(--white)}
.contact-list{list-style:none;font-size:6.5px;line-height:1.5}
.contact-list li{display:flex;gap:6px;margin-bottom:7px}
.contact-list svg{width:8px;height:8px;fill:var(--white);flex-shrink:0;margin-top:1px}

.bottom-bar{background:var(--blue-deep);height:36px;display:flex;justify-content:space-between;align-items:center;padding:0 40px;color:#cfe0ee;font-size:6px}
.bottom-nav a{color:#cfe0ee;text-decoration:none;margin-right:10px}
.bottom-nav p{margin-top:3px}
.social{display:flex;gap:4px}
.social span{width:12px;height:12px;background:var(--orange)}
</style>
</head>
<body>

<header class="site-header">
  <div class="brand"><span class="brand-mark"></span><span class="brand-name">KESTREL PHARMACY</span></div>
  <div class="header-contact">
    <strong>Contact us :</strong>
    <span><svg viewBox="0 0 10 10"><path d="M5 0a3.5 3.5 0 0 0-3.5 3.5C1.5 6 5 10 5 10s3.5-4 3.5-6.5A3.5 3.5 0 0 0 5 0zm0 5a1.5 1.5 0 1 1 0-3 1.5 1.5 0 0 1 0 3z"/></svg>Unit 2, 48 Alder Road, Riverton</span>
    <span><svg viewBox="0 0 10 10"><path d="M2 0l2 2.5-1 1.2c.6 1.3 1.6 2.3 2.8 2.9l1.2-1L9.5 7.5 8 10C3.5 9.5.5 6.5 0 2z"/></svg>08 9000 1234</span>
    <span>Western Australia</span>
    <span><svg viewBox="0 0 10 10"><path d="M0 2h10v6H0zM0 2l5 3.5L10 2" /></svg>care@kestrelpharmacy.example</span>
    <span><svg viewBox="0 0 10 10"><path d="M2 0l2 2.5-1 1.2c.6 1.3 1.6 2.3 2.8 2.9l1.2-1L9.5 7.5 8 10C3.5 9.5.5 6.5 0 2z"/></svg>08 9000 1235</span>
  </div>
</header>

<nav class="main-nav">
  <a class="active">HOME</a><a>ABOUT US</a><a>SERVICES</a><a>PRODUCTS</a><a>NEWS</a><a>LINKS</a><a>CONTACTS</a>
</nav>

<section class="hero" role="img" aria-label="Laboratory microscope with test tubes in a bright pharmacy preparation room">
  <span class="hero-arrow prev"><svg viewBox="0 0 6 8"><path d="M6 0v8L0 4z"/></svg></span>
  <div class="hero-text">
    <h1>COMPOUNDING PHARMACY</h1>
    <h2>IS CUSTOMISED MEDICATIONS FOR PATIENTS</h2>
    <span class="btn">GET MORE INFO ›</span>
  </div>
  <span class="hero-arrow next"><svg viewBox="0 0 6 8"><path d="M0 0v8l6-4z"/></svg></span>
</section>

<section class="intro">
  <h3>WHAT IS COMPOUNDING PHARMACY?</h3>
  <p>Compounding is the art and science of preparing personalised medications for patients. Our pharmacists combine or alter ingredients to create a medicine tailored to the needs of each individual, in a strength or form not available commercially. This long tradition remains at the heart of caring pharmacy practice today.</p>
</section>

<section class="values">
  <div class="value"><div class="value-icon"><svg viewBox="0 0 24 24"><path d="M4 5h7a2 2 0 0 1 2 2v12a2 2 0 0 0-2-2H4zM20 5h-7M20 5v12h-7"/></svg></div><h4>KNOWLEDGE AND SKILLS UPDATES</h4></div>
  <div class="value"><div class="value-icon"><svg viewBox="0 0 24 24"><path d="M12 3l2.7 5.6 6.1.9-4.4 4.3 1 6.1L12 17l-5.4 2.9 1-6.1-4.4-4.3 6.1-.9z"/></svg></div><h4>HIGHEST<br>STANDARDS</h4></div>
  <div class="value"><div class="value-icon"><svg viewBox="0 0 24 24"><circle cx="12" cy="12" r="8"/><path d="M8 12l3 3 5-6"/></svg></div><h4>QUALITY OF<br>SERVICE</h4></div>
  <div class="value"><div class="value-icon"><svg viewBox="0 0 24 24"><path d="M3 13l4-4 4 3 4-4 6 5M7 9v10M17 8v11"/></svg></div><h4>SUPPORT AN EFFECTIVE &amp; COMPETENT PRACTICE</h4></div>
  <div class="value"><div class="value-icon"><svg viewBox="0 0 24 24"><circle cx="12" cy="12" r="8"/><circle cx="12" cy="12" r="4"/><circle cx="12" cy="12" r=".8"/></svg></div><h4>OUR ULTIMATE<br>GOAL</h4></div>
</section>

<section class="features">
  <h3>Feature Items</h3>
  <div class="cards">
    <article class="card">
      <div class="card-photo vet" role="img" aria-label="Veterinarian caring for a pet"></div>
      <h5>Vet Article</h5>
      <p>Tailored medicines for animals, flavoured and dosed to suit each pet, prepared by our pharmacists together with your veterinarian.</p>
      <span class="more">READ MORE »</span>
    </article>
    <article class="card">
      <div class="card-photo oral" role="img" aria-label="Patient receiving oral therapy"></div>
      <h5>Oral Therapy</h5>
      <p>Liquids, lozenges and capsules made to your prescription, free of unwanted fillers and easier for patients to take every day.</p>
      <span class="more">READ MORE »</span>
    </article>
    <article class="card">
      <div class="card-photo thyroid" role="img" aria-label="Doctor examining a patient's thyroid"></div>
      <h5>Thyroid Extract</h5>
      <p>Carefully measured thyroid preparations compounded in our laboratory to the exact strength your doctor has prescribed for you.</p>
      <span class="more">READ MORE »</span>
    </article>
  </div>
  <div class="slider-dots">
    <span><svg viewBox="0 0 6 8"><path d="M6 0v8L0 4z"/></svg></span>
    <span><svg viewBox="0 0 6 8"><path d="M0 0v8l6-4z"/></svg></span>
  </div>
</section>

<footer class="site-footer">
  <div class="footer-col">
    <h6><svg viewBox="0 0 10 10"><path d="M5 0a5 5 0 1 0 0 10A5 5 0 0 0 5 0zm.6 5.3H3V4.2h1.5V2h1.1z"/></svg>Working Hours</h6>
    <table class="hours">
      <tr><td>Sunday</td><td>9:30 AM TO 6:30 PM</td></tr>
      <tr><td>Monday - Friday</td><td>8:30 AM TO 7:30 PM</td></tr>
      <tr><td>Saturday</td><td>8:30 AM TO 6:30 PM</td></tr>
    </table>
  </div>
  <div class="footer-col">
    <h6><svg viewBox="0 0 10 10"><path d="M5 0a3.5 3.5 0 0 0-3.5 3.5C1.5 6 5 10 5 10s3.5-4 3.5-6.5A3.5 3.5 0 0 0 5 0z"/></svg>Location</h6>
    <div class="map" role="img" aria-label="Street map showing the pharmacy location"></div>
  </div>
  <div class="footer-col">
    <h6><svg viewBox="0 0 10 10"><path d="M0 2h10v6H0z"/></svg>Contact Us</h6>
    <ul class="contact-list">
      <li><svg viewBox="0 0 10 10"><path d="M5 0a3.5 3.5 0 0 0-3.5 3.5C1.5 6 5 10 5 10s3.5-4 3.5-6.5A3.5 3.5 0 0 0 5 0z"/></svg><span>Unit 2, 48 Alder Road<br>Riverton WA<br>Western Australia</span></li>
      <li><svg viewBox="0 0 10 10"><path d="M2 0l2 2.5-1 1.2c.6 1.3 1.6 2.3 2.8 2.9l1.2-1L9.5 7.5 8 10C3.5 9.5.5 6.5 0 2z"/></svg><span>08 9000 1234</span></li>
      <li><svg viewBox="0 0 10 10"><path d="M2 0l2 2.5-1 1.2c.6 1.3 1.6 2.3 2.8 2.9l1.2-1L9.5 7.5 8 10C3.5 9.5.5 6.5 0 2z"/></svg><span>08 9000 1235</span></li>
      <li><svg viewBox="0 0 10 10"><path d="M0 2h10v6H0z"/></svg><span>care@kestrelpharmacy.example</span></li>
    </ul>
  </div>
</footer>

<div class="bottom-bar">
  <div class="bottom-nav">
    <a>Home</a><a>About Us</a><a>Services</a><a>Products</a><a>News</a><a>Links</a><a>Contacts</a>
    <p>Copyright © Kestrel Pharmacy 2024 , All Rights Reserved</p>
  </div>
  <div class="social"><span></span><span></span><span></span><span></span><span></span></div>
</div>

</body>
</html>
```